Blind Rivet Product catalogue

Need a design in wordpress with a productcatalogue where i present all products. This is a B2B business. The products is Blindrivets and Blindrivet nuts and accessories to this. I only want the basic information and also technical specification.

This is a subcompany to my existing company k7.m3.se but specializing in a subcategory

Businesses using blind rivet technology.

Industrial

Sans Serif

Must have
• Three different categories for the products; Blind Rivets - Blind Rivet Nut - Riveting Tools
Nice to have
• Possible to ad login for more information of the different sizes

```html
<!DOCTYPE html>
<html lang="en">
<head>
<meta charset="utf-8">
<title>K7M3 – Blind Rivet Catalogue</title>
<link href="https://fonts.googleapis.com/css2?family=Roboto:ital,wght@0,400;0,500;0,700;1,400&family=Rubik:wght@500;700&display=swap" rel="stylesheet">
<style>
:root{
  --red:#b5001b;
  --green:#3b9f0f;
  --black:#0d0d0d;
  --topbar:#1a1a1a;
  --footer:#1c1c1c;
  --grey-bg:#f1f1f1;
  --text:#222;
  --muted:#666;
  --white:#fff;
}
*{box-sizing:border-box;margin:0;padding:0}
html,body{width:1200px;height:3180px;overflow:hidden}
body{font-family:Roboto,sans-serif;color:var(--text);background:var(--white);position:relative}
h2.section-title{font-family:Rubik,sans-serif;font-weight:700;font-size:35px;text-align:center;letter-spacing:.3px;color:#111}
.btn{display:inline-flex;align-items:center;gap:8px;background:var(--green);color:#fff;font-weight:500;border-radius:30px;text-decoration:none}
.btn svg{width:15px;height:15px}

/* top bar */
.topbar{position:absolute;top:0;left:0;width:1200px;height:37px;background:var(--topbar);color:#eee;font-size:13px}
.topbar .item{position:absolute;top:0;height:37px;display:flex;align-items:center;gap:6px;padding:0 10px;border-right:1px solid #333}
.topbar svg{width:11px;height:11px;fill:#eee}

/* header */
.header{position:absolute;top:37px;left:0;width:1200px;height:87px;background:var(--black)}
.logo{position:absolute;left:111px;top:28px;display:flex;align-items:center;gap:8px;color:#fff;font-weight:700;font-size:24px}
.logo .mark{width:16px;height:16px;background:var(--green)}
.search{position:absolute;left:522px;top:24px;width:376px;height:43px;background:#fff;border-radius:22px;display:flex;align-items:center;font-size:12px}
.search .cat{width:140px;height:100%;background:#eee;border-radius:22px 0 0 22px;display:flex;align-items:center;padding:0 10px;color:#777;gap:24px;font-size:13px}
.search .field{flex:1;padding-left:22px;color:#777;font-size:11px}
.search .go{width:37px;height:37px;border-radius:50%;background:var(--green);margin-right:3px;display:flex;align-items:center;justify-content:center}
.cart{position:absolute;left:955px;top:24px;display:flex;align-items:center;gap:12px;color:#fff}
.cart .ic{width:42px;height:42px;border-radius:50%;background:var(--green);display:flex;align-items:center;justify-content:center}
.cart b{display:block;font-size:13px;font-weight:700}
.cart span{font-size:12px}
.cart em{font-style:normal;color:var(--red)}

/* nav */
.nav{position:absolute;top:124px;left:0;width:1200px;height:49px;background:var(--red)}
.nav ul{list-style:none;position:absolute;left:108px;right:108px;top:0;height:49px;display:flex;justify-content:space-between;align-items:center}
.nav li{color:#fff;font-weight:500;font-size:15px;position:relative;height:49px;line-height:49px;white-space:nowrap}
.nav li.active{color:#6ed43b}
.nav li.active::after{content:"";position:absolute;left:0;right:0;bottom:2px;height:4px;background:var(--green)}

/* hero */
.hero{position:absolute;top:173px;left:0;width:1200px;height:536px;background:linear-gradient(90deg,#eceef0 0%,#dfe2e5 45%,#c9ccd0 100%)}
.hero .photo{position:absolute;left:560px;top:0;width:640px;height:536px;background:radial-gradient(ellipse at 55% 45%,#d9531e 0%,#b8572c 16%,#8f6a58 30%,#c7c9cc 55%,transparent 70%)}
.hero h1{position:absolute;left:111px;top:160px;font-family:Rubik,sans-serif;font-weight:700;font-size:46px;color:#111}
.hero p{position:absolute;left:111px;top:232px;width:420px;font-size:19px;line-height:27px;color:#111}
.hero .btn{position:absolute;left:111px;top:307px;height:54px;padding:0 27px;font-size:18px}
.dots{position:absolute;left:573px;top:482px;display:flex;gap:8px}
.dots i{width:12px;height:12px;border-radius:50%;border:2px solid #222;display:block}
.dots i.on{border-color:var(--green);background:radial-gradient(circle,var(--green) 35%,transparent 40%)}

/* about */
.about-img{position:absolute;left:111px;top:809px;width:478px;height:345px;background:linear-gradient(160deg,#7d8ea6 0%,#b7c0cb 40%,#8f979f 70%,#5f666d 100%);box-shadow:-9px 9px 0 var(--red)}
.about-text{position:absolute;left:650px;top:815px;width:439px}
.about-text h2{font-family:Rubik,sans-serif;font-weight:700;font-size:34px;margin-bottom:22px}
.about-text p{font-size:15px;line-height:26.5px;color:#555;text-align:justify}
.about-text .btn{margin-top:25px;height:50px;padding:0 24px;font-size:15px}

/* featured */
.featured{position:absolute;top:1281px;left:0;width:1200px;height:554px;background:var(--grey-bg)}
.featured h2{position:absolute;top:42px;left:0;width:1200px}
.card{position:absolute;top:123px;width:295px;text-align:center}
.card .thumb{height:167px;background:#fff;box-shadow:0 0 6px rgba(0,0,0,.08);position:relative}
.card .thumb .ph{position:absolute;left:75px;top:12px;width:145px;height:140px;border-radius:50%;background:radial-gradient(circle,#c8c8c8 0%,#e9e9e9 65%,#fff 72%)}
.card .tag{position:absolute;right:0;top:12px;background:#222;color:#fff;font-size:11px;padding:3px 4px 3px 12px;clip-path:polygon(8px 0,100% 0,100% 100%,8px 100%,0 50%)}
.card .tools{position:absolute;left:15px;top:10px;display:flex;flex-direction:column;gap:3px}
.card .tools i{width:24px;height:24px;background:#222;display:block}
.card h3{font-size:16px;font-weight:500;margin-top:22px;color:#111}
.card p{font-size:14px;line-height:21px;color:#666;margin-top:18px}
.card .btn{margin-top:20px;height:38px;padding:0 18px;border-radius:3px;font-size:13px;font-weight:700}

/* testimonials */
.testi{position:absolute;top:1835px;left:0;width:1200px;height:320px;background:var(--red);color:#fff}
.testi h2{position:absolute;top:48px;left:0;width:1200px;color:#fff}
.testi .avatar{position:absolute;left:183px;top:117px;width:94px;height:94px;transform:rotate(45deg);background:linear-gradient(135deg,#5fb0e6,#2b6ea8);border:3px solid #fff}
.testi .quote{position:absolute;left:321px;top:132px;width:680px;font-style:italic;font-size:15.5px;line-height:27px}
.testi .q{position:absolute;font-family:Georgia,serif;font-size:60px;color:#e47a84;line-height:1}
.testi .q-end{font-family:Georgia,serif;font-style:normal;font-size:50px;color:#e47a84;line-height:0;vertical-align:-22px;margin-left:8px}
.testi .name{position:absolute;left:321px;top:232px;font-size:18px;font-weight:500}
.testi .co{position:absolute;left:321px;top:261px;font-size:12px}
.arrow{position:absolute;top:114px;width:30px;height:50px}

/* news */
.news h2{position:absolute;top:2257px;left:0;width:1200px}
.post{position:absolute;top:2333px;width:307px}
.post .img{height:204px}
.post .box{position:relative;margin:-40px 13px 0;background:#fff;box-shadow:0 2px 8px rgba(0,0,0,.1);padding:22px 16px 20px;height:161px}
.post .label{display:inline-block;background:var(--red);color:#fff;font-size:13px;font-weight:500;padding:5px 6px}
.post h3{font-size:15.5px;font-weight:500;line-height:22px;margin-top:14px;color:#111}
.post .meta{font-size:13.5px;color:#666;margin-top:10px;display:flex;gap:10px;align-items:center}
.post .meta b{color:var(--red);font-weight:400}

/* footer */
.footer{position:absolute;top:2769px;left:0;width:1200px;height:411px;background:var(--footer);color:#fff}
.fcol{position:absolute;top:89px}
.fcol h4{font-size:16px;font-weight:700;margin-bottom:28px}
.fcol li{list-style:none;font-size:14px;margin-bottom:13px}
.contact li{display:flex;gap:12px;line-height:18px}
.contact svg{width:13px;height:13px;fill:#fff;flex:none;margin-top:2px}
.social li{display:flex;align-items:center;gap:12px;margin-bottom:7px}
.social i{width:29px;height:29px;border-radius:50%;background:#3a3a3a;display:block}
.footer hr{position:absolute;left:111px;top:320px;width:1006px;border:0;border-top:1px solid #444}
.cards{position:absolute;left:520px;top:336px;display:flex;gap:3px}
.cards i{width:32px;height:20px;background:#fff;border-radius:2px;display:block}
.copy{position:absolute;top:367px;left:0;width:1200px;text-align:center;font-size:14px}
</style>
</head>
<body>

<div class="topbar">
  <div class="item" style="left:103px"><svg viewBox="0 0 10 10"><path d="M5 0a3.5 3.5 0 0 0-3.5 3.5C1.5 6 5 10 5 10s3.5-4 3.5-6.5A3.5 3.5 0 0 0 5 0zm0 5a1.5 1.5 0 1 1 0-3 1.5 1.5 0 0 1 0 3z"/></svg>Store Location</div>
  <div class="item" style="left:222px"><svg viewBox="0 0 10 10"><circle cx="5" cy="3" r="2.5"/><path d="M0 10c0-3 2-4.5 5-4.5s5 1.5 5 4.5z"/></svg>Login/Register</div>
  <div class="item" style="left:353px"><svg viewBox="0 0 10 10"><rect x="0" y="2" width="6" height="5"/><path d="M6 4h2.5L10 6v1H6z"/><circle cx="2" cy="8.5" r="1.2"/><circle cx="8" cy="8.5" r="1.2"/></svg>Track Orders</div>
  <div class="item" style="left:780px;border-left:1px solid #333"><svg viewBox="0 0 10 10"><path d="M2 0l2 2.5-1.2 1.3a6 6 0 0 0 3.4 3.4L7.5 6 10 8l-1.5 2C4 10 0 6 0 1.5z"/></svg>Hotline:&nbsp; 888 888 8888</div>
  <div class="item" style="left:948px">English ⌄</div>
  <div class="item" style="left:1027px;border-right:0">$ USD ⌄</div>
</div>

<div class="header">
  <div class="logo"><span class="mark"></span>K7M3</div>
  <div class="search">
    <div class="cat">All Categories <span>▾</span></div>
    <div class="field">Search Product</div>
    <div class="go"><svg width="15" height="15" viewBox="0 0 16 16"><circle cx="6.5" cy="6.5" r="4.5" fill="none" stroke="#fff" stroke-width="2.5"/><path d="M10 10l4 4" stroke="#fff" stroke-width="2.5"/></svg></div>
  </div>
  <div class="cart">
    <div class="ic"><svg width="20" height="18" viewBox="0 0 20 18"><path d="M0 1h3l3 10h10l3-7H5" fill="none" stroke="#fff" stroke-width="2"/><circle cx="7" cy="15" r="1.8" fill="#fff"/><circle cx="15" cy="15" r="1.8" fill="#fff"/></svg></div>
    <div><b>MY CART</b><span>0 item- <em>$0.00</em></span></div>
  </div>
</div>

<nav class="nav"><ul>
  <li class="active">Blind Rivets</li><li>Blind Rivet Nuts</li><li>Riveting Tools</li><li>Accessories</li><li>Other attachment</li><li>Contact Us</li><li>About us</li><li>Sitemap</li>
</ul></nav>

<section class="hero">
  <div class="photo" role="img" aria-label="Hand drilling into a white wall with an orange power drill"></div>
  <h1>K7M3</h1>
  <p>K7M3 AB is a wholesale company that caters to other companies.</p>
  <a class="btn" href="#">SHOP NOW <svg viewBox="0 0 16 16"><circle cx="8" cy="8" r="8" fill="#fff"/><path d="M5 8h6M8 5l3 3-3 3" stroke="#3b9f0f" stroke-width="2" fill="none"/></svg></a>
  <div class="dots"><i></i><i class="on"></i><i></i></div>
</section>

<section class="about">
  <div class="about-img" role="img" aria-label="Steel ladder with safety cage seen from below against a cloudy sky"></div>
  <div class="about-text">
    <h2>ABOUT K7M3</h2>
    <p>K7M3 AB is a wholesale company that caters to other companies. Our range consists of stainless steel products for mounting and marine applications. We have the widest and deepest range of stainless steel on the market. Our attachments comply with DIN standards and ISO standards.<br>Prices shown on our website are gross prices, to get prices that apply to your business please contact us.</p>
    <a class="btn" href="#">LEARN MORE <svg viewBox="0 0 16 16"><circle cx="8" cy="8" r="8" fill="#fff"/><path d="M5 8h6M8 5l3 3-3 3" stroke="#3b9f0f" stroke-width="2" fill="none"/></svg></a>
  </div>
</section>

<section class="featured">
  <h2 class="section-title">FEATURED PRODUCTS</h2>
  <div class="card" style="left:112px">
    <div class="thumb"><div class="ph" role="img" aria-label="Steel blind rivet nut"></div><span class="tag">FEATURED</span><div class="tools"><i></i><i></i></div></div>
    <h3>Blind- Rivet- Nuts</h3>
    <p>Lorem ipsum dolor amet, consectetur<br>adipiscing elit, sed do</p>
    <a class="btn" href="#">SHOP NOW <svg viewBox="0 0 16 16"><circle cx="8" cy="8" r="8" fill="#fff"/><path d="M5 8h6M8 5l3 3-3 3" stroke="#3b9f0f" stroke-width="2" fill="none"/></svg></a>
  </div>
  <div class="card" style="left:452px">
    <div class="thumb"><div class="ph" role="img" aria-label="Battery driven riveting tool"></div><span class="tag">FEATURED</span></div>
    <h3>Battery-Driven-Tools-Riveting-Tools</h3>
    <p>Lorem ipsum dolor amet, consectetur<br>adipiscing elit, sed do</p>
    <a class="btn" href="#">SHOP NOW <svg viewBox="0 0 16 16"><circle cx="8" cy="8" r="8" fill="#fff"/><path d="M5 8h6M8 5l3 3-3 3" stroke="#3b9f0f" stroke-width="2" fill="none"/></svg></a>
  </div>
  <div class="card" style="left:793px">
    <div class="thumb"><div class="ph" role="img" aria-label="Steel blind rivet"></div><span class="tag">FEATURED</span></div>
    <h3>Blind- Rivets</h3>
    <p>Lorem ipsum dolor amet, consectetur<br>adipiscing elit, sed do</p>
    <a class="btn" href="#">SHOP NOW <svg viewBox="0 0 16 16"><circle cx="8" cy="8" r="8" fill="#fff"/><path d="M5 8h6M8 5l3 3-3 3" stroke="#3b9f0f" stroke-width="2" fill="none"/></svg></a>
  </div>
</section>

<section class="testi">
  <h2 class="section-title">WHAT OUR CLIENTS HAVE TO SAY</h2>
  <svg class="arrow" style="left:106px" viewBox="0 0 30 50"><path d="M24 6L8 25l16 19" stroke="#e9b3b9" stroke-width="5" fill="none"/></svg>
  <svg class="arrow" style="left:1062px" viewBox="0 0 30 50"><path d="M6 6l16 19-16 19" stroke="#e9b3b9" stroke-width="5" fill="none"/></svg>
  <div class="avatar" role="img" aria-label="Client portrait"></div>
  <span class="q" style="left:280px;top:110px">“</span>
  <p class="quote">Lorem ipsum dolor sit amet, consectetur adipiscing elit, sed do eiusmod tempor incididunt ut labore et dolore magna aliqua. Ut enim ad minim veniam, quis nostrud exercitation ullamco laboris nisi ut aliquip ex ea commodo consequat.<span class="q-end">”</span></p>
  <div class="name">John Doe</div>
  <div class="co">Company Name</div>
</section>

<section class="news">
  <h2 class="section-title">OUR NEWS</h2>
  <article class="post" style="left:111px">
    <div class="img" role="img" aria-label="Solar panels under blue sky" style="background:linear-gradient(150deg,#9cc0e8,#3c6fb4 55%,#24447e)"></div>
    <div class="box"><span class="label">Lorem ipsum</span><h3>Lorem ipsum dolor sit consectetur adipiscing elit, sed do</h3><div class="meta"><span><b>●</b> By, David</span>|<span><b>▦</b> March 05, 2020</span></div></div>
  </article>
  <article class="post" style="left:446px">
    <div class="img" role="img" aria-label="Worker wearing leather work gloves" style="background:linear-gradient(135deg,#4a3c2c,#c48a2a 45%,#e8c27a 60%,#3a3026)"></div>
    <div class="box"><span class="label">Lorem ipsum</span><h3>Lorem ipsum dolor sit consectetur adipiscing elit, sed do</h3><div class="meta"><span><b>●</b> By, David</span>|<span><b>▦</b> March 05, 2020</span></div></div>
  </article>
  <article class="post" style="left:781px">
    <div class="img" role="img" aria-label="Industrial pipework in a factory" style="background:linear-gradient(135deg,#1f3a7a,#4d7fc2 40%,#c94a3a 75%,#2a2a4a)"></div>
    <div class="box"><span class="label">Lorem ipsum</span><h3>Lorem ipsum dolor sit consectetur adipiscing elit, sed do</h3><div class="meta"><span><b>●</b> By, David</span>|<span><b>▦</b> March 05, 2020</span></div></div>
  </article>
</section>

<footer class="footer">
  <div class="fcol contact" style="left:111px;width:200px">
    <h4>CONTACT US</h4>
    <ul>
      <li><svg viewBox="0 0 10 10"><path d="M5 0a3.5 3.5 0 0 0-3.5 3.5C1.5 6 5 10 5 10s3.5-4 3.5-6.5A3.5 3.5 0 0 0 5 0zm0 5a1.5 1.5 0 1 1 0-3 1.5 1.5 0 0 1 0 3z"/></svg>123, Lorem ipsum dolor sit amet - 12345</li>
      <li><svg viewBox="0 0 10 10"><path d="M0 2h10v6H0z M0 2l5 3.5L10 2" /></svg>info@k7m3.com</li>
      <li><svg viewBox="0 0 10 10"><path d="M2 0l2 2.5-1.2 1.3a6 6 0 0 0 3.4 3.4L7.5 6 10 8l-1.5 2C4 10 0 6 0 1.5z"/></svg>888 888 8888</li>
    </ul>
  </div>
  <div class="fcol" style="left:370px"><h4 style="margin-left:2px">CATEGORIES</h4><ul><li>Blind Rivets</li><li>Blind Rivet Nuts</li><li>Riveting Tools</li><li>Accessories</li></ul></div>
  <div class="fcol" style="left:586px"><h4 style="margin-left:2px">ABOUT</h4><ul><li>History</li><li>News</li><li>Careers</li><li>Locations</li></ul></div>
  <div class="fcol" style="left:758px"><h4 style="margin-left:2px">OTHER LINKS</h4><ul><li>Privacy Policy</li><li>Terms &amp; Conditions</li><li>FAQ</li><li>Sitemap</li></ul></div>
  <div class="fcol social" style="left:972px"><h4>FOLLOW US</h4><ul style="margin-top:-12px"><li><i></i>Friendnet</li><li><i></i>Chirper</li><li><i></i>Circles Plus</li><li><i></i>Worklink</li></ul></div>
  <hr>
  <div class="cards"><i></i><i></i><i></i><i></i><i></i></div>
  <div class="copy">Copyrights © k7m3 2020 | Allrights Reserved</div>
</footer>

</body>
</html>
```